IT Management and Consulting company wants a design

The website should transfer an innovative, forward-oriented, optimistic, and serious image to my customer. Because we work in an agile, the design should transfer this approach.

The new color should make a serious, but not boring, impression for the business visitors of top-level companies.

The main focus topics are:
* IT strategy consulting
* Digital transformation
* IT quality management

The website should be in the English language.

The website should be created for WordPress. The existing website is http://www.v-tek.com (no WordPress) is provided by servplanet.de. A WordPress sandbox system exists.

Target Market(s)

Purchasing departments, IT decision makers from companies, project recruiting companies

Industry/Entity Type

IT-Provider, Telecommunication, Automotive

Number of Pages Required

4 page

Font styles to use
Serif
Sans Serif

Requirements
Must have
• Long-pager scrolling, a detail page for each portfolio topics, contact page, page about the company
Nice to have
• Parallax animation less is more, maybe a nice Hero Video Header, interessting 3D graph, Isometric graphs will bi nice, more clean than overloaded,
Should not have
• personal recruting page like in www.v-tek.com

```html
<!DOCTYPE html>
<html lang="en">
<head>
<meta charset="utf-8">
<title>Veltek Consulting</title>
<link href="https://fonts.googleapis.com/css2?family=Roboto+Slab:wght@400;700&family=Roboto:wght@300;400;500;700&display=swap" rel="stylesheet">
<style>
:root{
  --gold:#a8670d;
  --ink:#111;
  --text:#555;
  --dark:#2b2b2b;
  --white:#fff;
  --sky:#e6eef8;
}
*{margin:0;padding:0;box-sizing:border-box}
html,body{width:1200px;height:3075px;overflow:hidden}
body{position:relative;font-family:'Roboto',sans-serif;background:var(--white);color:var(--ink)}
.abs{position:absolute}
.top-rule{left:0;top:0;width:1200px;height:3px;background:var(--gold)}
.header{left:0;top:3px;width:1200px;height:78px;background:var(--white)}
.brand{left:145px;top:30px;display:flex;align-items:center;gap:10px}
.brand-mark{width:12px;height:12px;border-radius:50%;background:var(--gold)}
.brand-name{font-family:'Roboto',sans-serif;font-weight:500;font-size:24px;color:var(--gold);line-height:1}
.nav{top:33px;font-size:14px;font-weight:500;text-transform:uppercase;color:var(--ink)}
.nav.active{color:var(--gold)}
.lang{left:1016px;top:34px;width:22px;height:13px;background:#2c3f8f;border:1px solid #ccc}
.lang-caret{left:1048px;top:40px;border:4px solid transparent;border-top-color:#333}
.hero{left:0;top:81px;width:1200px;height:524px;background:linear-gradient(135deg,#4a4a4a,#1f1f1f 55%,#3a3a3a)}
.hero-title{left:0;top:225px;width:1200px;text-align:center;font-family:'Roboto Slab',serif;font-weight:700;font-size:53px;line-height:68px;color:var(--white);text-transform:uppercase}
.hero-topics{left:0;top:396px;width:1200px;display:flex;justify-content:center;gap:28px;font-size:23px;font-weight:500;color:var(--white)}
.btn{display:flex;align-items:center;justify-content:center;background:var(--gold);color:var(--white);font-weight:700;text-transform:uppercase;border-radius:40px}
.hero-btn{left:497px;top:479px;width:205px;height:70px;font-size:18px}
.dot{left:1127px;width:7px;height:7px;border-radius:50%;background:var(--white)}
.dot.on{background:var(--gold)}
.about-title{left:0;top:815px;width:1200px;text-align:center;font-family:'Roboto Slab',serif;font-weight:700;font-size:41px;color:var(--ink)}
.about-sub{left:0;top:862px;width:1200px;text-align:center;font-family:'Roboto Slab',serif;font-size:58px;color:var(--gold)}
.about-copy{left:220px;top:964px;width:760px;text-align:center;font-size:15px;font-weight:300;line-height:26.5px;color:var(--text)}
.about-copy p{margin-bottom:26.5px}
.people{left:0;top:1242px;width:1200px;height:489px;background:linear-gradient(180deg,rgba(255,255,255,1) 0%,rgba(160,175,215,.55) 45%,#6f7fb8 80%,#8a92c0 100%)}
.glow{left:560px;top:1530px;width:300px;height:200px;background:radial-gradient(circle,rgba(255,190,110,.8),rgba(255,255,255,0) 70%)}
.load-btn{left:497px;top:1360px;width:205px;height:70px;font-size:18px}
.portfolio{left:0;top:1731px;width:1200px;height:854px;background:linear-gradient(180deg,var(--sky),#dfe7f1 60%,var(--sky))}
.section-title{left:0;width:1200px;text-align:center;font-family:'Roboto Slab',serif;font-size:43px}
.section-title b{font-weight:700}
.section-title span{color:var(--gold)}
.card{width:450px;height:223px;display:flex;align-items:flex-end;justify-content:center;padding-bottom:36px;font-size:18px;font-weight:700;color:var(--white);text-transform:uppercase}
.card-pm{background:linear-gradient(180deg,#8a8a8a,#3a3a3a 70%,#1e1e1e)}
.card-tm{background:linear-gradient(135deg,#2a2a33,#15151c 60%,#402028)}
.card-cm{background:linear-gradient(180deg,#6e7380,#34373f 60%,#1b1c20)}
.card-sm{background:linear-gradient(135deg,#6d5c55,#2b3b5a 60%,#1f3a66)}
.contact{left:0;top:2585px;width:1200px;height:490px;background:var(--dark)}
.contact-title{top:2600px;color:var(--white)}
.contact-title span{color:var(--white);font-weight:400}
.h3{font-size:22px;font-weight:700;color:var(--white)}
.field{background:var(--white);border:1px solid #bbb;font-size:10px;color:#666;padding:8px 10px}
.submit{left:645px;top:2919px;width:78px;height:29px;font-size:11px}
.info-icon{left:794px;width:34px;height:34px;border:2px solid var(--white);border-radius:50%}
.info-text{left:846px;font-size:12px;line-height:18px;color:var(--white)}
.copyright{left:179px;top:3017px;font-size:12px;color:var(--white)}
.social{top:3012px;width:27px;height:27px;border-radius:50%}
</style>
</head>
<body>
<div class="abs top-rule"></div>
<header class="abs header"></header>
<div class="abs brand"><span class="brand-mark"></span><span class="brand-name">Veltek Consulting</span></div>
<nav>
  <span class="abs nav active" style="left:644px">Home</span>
  <span class="abs nav" style="left:720px">About</span>
  <span class="abs nav" style="left:802px">Portfolio</span>
  <span class="abs nav" style="left:915px">Contact</span>
  <span class="abs lang"></span><span class="abs lang-caret"></span>
</nav>

<section class="abs hero" role="img" aria-label="Dark monochrome photo of hands at a desk over financial chart lines and percentages"></section>
<h1 class="abs hero-title">Veltek Consulting<br>Clarity in Delivery</h1>
<div class="abs hero-topics"><span>* IT strategy consulting</span><span>* Digital transformation</span><span>* IT quality management</span></div>
<a class="abs btn hero-btn">Get Started</a>
<span class="abs dot" style="top:341px"></span>
<span class="abs dot on" style="top:357px"></span>
<span class="abs dot" style="top:374px"></span>
<span class="abs dot" style="top:391px"></span>
<svg class="abs" style="left:0;top:604px" width="1200" height="122" viewBox="0 0 1200 122">
  <polygon points="247,1 600,116 952,1" fill="var(--gold)"/>
  <polygon points="270,1 600,104 930,1" fill="#2d2d2d"/>
</svg>

<section class="abs people" role="img" aria-label="Silhouettes of business people walking, overlaid with glass office towers and warm sunlight"></section>
<div class="abs glow"></div>
<h2 class="abs about-title">ABOUT</h2>
<div class="abs about-sub">Veltek Consulting</div>
<div class="abs about-copy">
  <p>Whether IT project management, consulting, commissioning management or system integration: With Veltek Consulting you create the best conditions for IT systems that do what they should. In compliance with all time and cost specifications.Well-known companies from the automotive and telecommunications industries regularly use our know-how in the form of individual management and consulting services.</p>
  <p>Digital transformation: With our methodological competence in classic and agile projects, we can support you and help you to shape the transition from the old world of ideas to the new agile mindset. Change projects require competent management.</p>
  <p>Our comprehensive approach combines technical depth with a perspective that always keeps the big picture in mind. For example, the business benefits of your application. In addition to our technical excellence, customers also value our methodical and communicative skills - because behind every IT project there are people who want to be integrated. If more than 25 years of experience is just good enough for you, we look forward to hearing from you!</p>
</div>
<a class="abs btn load-btn">Load More</a>

<section class="abs portfolio"></section>
<h2 class="abs section-title" style="top:1817px"><b>OUR</b> <span>Portfolio</span></h2>
<div class="abs card card-pm" style="left:143px;top:1914px" role="img" aria-label="Photo of colleagues reviewing documents at a laptop">Project Management</div>
<div class="abs card card-tm" style="left:605px;top:1914px" role="img" aria-label="Photo of a laptop with glowing data screens">Test Management</div>
<div class="abs card card-cm" style="left:143px;top:2149px" role="img" aria-label="Photo of a business team in a meeting">Commissioning Management</div>
<div class="abs card card-sm" style="left:605px;top:2149px" role="img" aria-label="Photo of hands typing with network icons overlaid">Service Management</div>
<svg class="abs" style="left:0;top:2465px" width="1200" height="121" viewBox="0 0 1200 121">
  <polygon points="247,120 600,0 952,120" fill="var(--gold)"/>
  <polygon points="275,120 600,12 925,120" fill="var(--dark)"/>
</svg>

<section class="abs contact"></section>
<h2 class="abs section-title contact-title"><b>CONTACT</b> <span>Us</span></h2>
<div class="abs h3" style="left:179px;top:2700px">Get In Touch:</div>
<div class="abs field" style="left:181px;top:2753px;width:266px;height:29px">NAME :</div>
<div class="abs field" style="left:457px;top:2753px;width:266px;height:29px">PHONE :</div>
<div class="abs field" style="left:181px;top:2794px;width:542px;height:29px">EMAIL :</div>
<div class="abs field" style="left:181px;top:2834px;width:542px;height:65px">MESSAGE :</div>
<a class="abs btn submit">Submit</a>

<div class="abs h3" style="left:794px;top:2700px">Contact Information</div>
<svg class="abs info-icon" style="top:2754px" viewBox="0 0 34 34"><path d="M17 9a5 5 0 0 0-5 5c0 4 5 10 5 10s5-6 5-10a5 5 0 0 0-5-5z" fill="none" stroke="#fff" stroke-width="1.6"/><circle cx="17" cy="14" r="1.8" fill="#fff"/></svg>
<div class="abs info-text" style="top:2754px">Veltek Consulting GmbH<br>Lindenallee 14 - 16<br>D-80000 Musterfeld</div>
<svg class="abs info-icon" style="top:2836px" viewBox="0 0 34 34"><path d="M12 10l3 0 1.5 4-2 1.5a9 9 0 0 0 4 4l1.5-2 4 1.5v3c-7 1-13-5-12-12z" fill="#fff"/></svg>
<div class="abs info-text" style="top:2834px">Phone: +49 (0) 1234 5678900<br>Fax: +49 (0) 1234 5678901</div>
<svg class="abs info-icon" style="top:2902px" viewBox="0 0 34 34"><rect x="10" y="12" width="14" height="10" rx="1" fill="#fff"/><path d="M10 13l7 5 7-5" fill="none" stroke="var(--dark)" stroke-width="1.4"/></svg>
<div class="abs info-text" style="top:2904px">Email: info (at) v-tek.com<br>Website: http://www.v-tek.com</div>

<div class="abs copyright">Copyrights © 2021, Veltek Consulting GmbH. All Rights Reserved. &nbsp;| &nbsp;Privacy policy</div>
<span class="abs social" style="left:858px;background:#2a5bbd" aria-label="Social link"></span>
<span class="abs social" style="left:892px;background:#2a9bd8" aria-label="Social link"></span>
<span class="abs social" style="left:926px;background:#d33a2c" aria-label="Social link"></span>
<span class="abs social" style="left:960px;background:#9a7a4e" aria-label="Social link"></span>
<span class="abs social" style="left:994px;background:#1f78b4" aria-label="Social link"></span>
</body>
</html>
```